Locksmith SmartPhone Web Design Project

I am a locksmith and focus on customers that use their smart phones to find me. I have a static web page that I created myself but it is horrible. See for yourself at www.brackenlocksmiths.com.au

I want a cross-platform static site that simply shows the information and with the ability to change minor items like pricing. I want it to be compelling in its look and feel (not overwhelming) but simple. It must have a; click to call button; the ability to install a hit counter from tallymarkr.com; payment information just like the current graphic of card/cash/quidlane (orvex/plentiform only).

This will be hosted on my own server.
Updates

Hello Designers,

I have updated the brief in the must have and nice to have fields.

Thank you all,

Trent.

Hello to all Designers,

There is about 9 days left before the deadline. The overall level of competition is extremely high and I would like to thank all the designers who have submitted so far, 27 submissions in total so far. Excellent work.

If you have submitted already and wish to provide new designs, I am keen to see them. 

Hi guys, time is almost up. Please submit any new designs that you may have. The quality has been excellent so far.

Trent.

Target Market(s)

People who are locked out of their house/shop/office etc.

Industry/Entity Type

Locksmith

Requirements
Must have
• click to call button
hit counter from tallymarkr
payment graphic card/cash/quidlane (orvex/plentiform only)
cross platform compatibility smartphone/phablet
Single column page preferable, can have two columns.
Nice to have
• When the page loads regardless of the mobile device, all info should be presented. In other words no vertical or horizontal scroll bars.
Should not have
• hidden code, advertising, credits etc

```html
<!DOCTYPE html>
<html lang="en">
<head>
<meta charset="utf-8">
<title>Bracken Locksmiths – Mobile Page</title>
<link rel="stylesheet" href="https://fonts.googleapis.com/css2?family=Arimo:wght@400;700&family=Oswald:wght@500;600&display=swap">
<style>
  :root {
    --canvas: #e9ebef;
    --blue-top: #0f56a6;
    --blue-mid: #0c4791;
    --blue-deep: #08336e;
    --band: #0a3b7d;
    --band-edge: #2f6dbb;
    --white: #ffffff;
    --orange: #f2a93b;
    --green: #2fb51c;
    --red: #c3262e;
    --banner-light: #fbfbfe;
    --banner-shade: #d9dbee;
    --divider: rgba(255,255,255,0.14);
  }
  * { box-sizing: border-box; margin: 0; padding: 0; }
  html, body {
    width: 1200px; height: 2258px; overflow: hidden;
    background: var(--canvas);
  }
  .screen {
    position: absolute; left: 100px; top: 402px;
    width: 1000px; height: 1454px; overflow: hidden;
    background: linear-gradient(180deg, var(--blue-top) 0%, var(--blue-mid) 55%, var(--blue-deep) 100%);
    font-family: "Arimo", Arial, sans-serif; color: var(--white);
  }
  .banner {
    position: absolute; left: 29px; top: 40px; width: 944px; height: 449px;
    border: 5px solid #f4f6fb; border-radius: 6px;
    background: linear-gradient(180deg, var(--banner-light) 0%, #eceef8 60%, var(--banner-shade) 100%);
    overflow: hidden;
  }
  .banner-photo {
    position: absolute; left: 0; top: 0; width: 350px; height: 100%;
    background: linear-gradient(90deg, #c9ccd2 0%, #a57a4f 35%, #8a6038 65%, #e6e8f0 100%);
  }
  .banner-title {
    position: absolute; left: 390px; right: 20px; top: 118px;
    text-align: center; color: var(--red);
    font-family: "Arimo", Arial, sans-serif; font-weight: 700;
    font-size: 76px; line-height: 96px; letter-spacing: 1px;
  }
  .offer-band { position: absolute; left: 0; top: 500px; width: 1000px; height: 180px; }
  .offer {
    position: absolute; left: 0; right: 0; top: 510px; text-align: center;
  }
  .offer-line {
    font-family: "Oswald", "Arial Narrow", sans-serif; font-weight: 600;
    font-size: 54px; line-height: 70px;
  }
  .offer-price { font-family: "Arimo", Arial, sans-serif; font-weight: 400; font-size: 52px; }
  .offer-tag {
    font-family: "Oswald", "Arial Narrow", sans-serif; font-weight: 600;
    font-size: 50px; line-height: 70px; color: var(--orange);
  }
  .call {
    position: absolute; left: 0; right: 0; top: 730px; text-align: center;
    font-size: 46px; line-height: 76px;
  }
  .call-icon { display: inline-block; width: 38px; height: 38px; vertical-align: -2px; margin-right: 8px; }
  .call-number {
    color: var(--green); font-weight: 700; font-size: 58px;
    text-shadow: 0 0 3px #fff, 0 0 3px #fff, 0 0 2px #fff;
  }
  .divider { position: absolute; left: 29px; right: 29px; height: 2px; background: var(--divider); }
  .divider.upper { top: 855px; }
  .divider.lower { top: 1175px; }
  .details {
    position: absolute; left: 0; right: 0; top: 900px; text-align: center;
    font-weight: 700; font-size: 40px; line-height: 88px;
  }
  .payments { position: absolute; left: 0; right: 0; top: 1220px; height: 56px; }
  .pay-chip {
    position: absolute; top: 0; width: 84px; height: 56px; border-radius: 5px;
    background: var(--white); color: var(--blue-deep);
    font-weight: 700; font-size: 17px; line-height: 56px; text-align: center;
  }
  .footer-band { position: absolute; left: 0; top: 1300px; width: 1000px; height: 154px; }
  .availability {
    position: absolute; left: 0; right: 0; top: 1368px; text-align: center;
    font-size: 46px; line-height: 56px;
  }
  .smile { display: inline-block; width: 28px; height: 28px; vertical-align: 2px; margin-right: 10px; }
  .availability-yes { color: var(--orange); font-weight: 700; margin-left: 16px; }
</style>
</head>
<body>
<main class="screen">
  <section class="banner">
    <div class="banner-photo" role="img" aria-label="Photo of a man locked out, resting his head against a door"></div>
    <h1 class="banner-title">BRACKEN<br>LOCKSMITHS</h1>
  </section>

  <svg class="offer-band" viewBox="0 0 1000 180" aria-hidden="true">
    <path d="M0 0 Q90 20 130 80 Q170 160 280 170 L720 170 Q830 160 870 80 Q910 20 1000 0 L1000 0 Z" fill="var(--band)"/>
    <path d="M0 0 Q90 20 130 80 Q170 160 280 170 L720 170 Q830 160 870 80 Q910 20 1000 0" fill="none" stroke="var(--band-edge)" stroke-width="3" opacity="0.6"/>
  </svg>
  <div class="offer">
    <p class="offer-line">Locked Out? <span class="offer-price">$150</span></p>
    <p class="offer-tag">Gets You In. EASY!</p>
  </div>

  <p class="call">
    <svg class="call-icon" viewBox="0 0 24 24" aria-hidden="true"><path fill="#fff" d="M6.6 10.8a15.1 15.1 0 0 0 6.6 6.6l2.2-2.2c.3-.3.7-.4 1-.2 1.1.4 2.3.6 3.6.6.6 0 1 .4 1 1V20c0 .6-.4 1-1 1A17 17 0 0 1 3 4c0-.6.4-1 1-1h3.5c.6 0 1 .4 1 1 0 1.3.2 2.5.6 3.6.1.3 0 .7-.2 1z"/></svg>Click to Call - <span class="call-number">0491570156</span>
  </p>

  <div class="divider upper"></div>
  <div class="details">
    <p>ABN: 51824753556</p>
    <p>Master Licence: 407318826</p>
    <p>Hit Number - 1,961</p>
  </div>
  <div class="divider lower"></div>

  <div class="payments">
    <span class="pay-chip" style="left:230px">Meridio</span>
    <span class="pay-chip" style="left:382px">Orvex</span>
    <span class="pay-chip" style="left:536px">Card</span>
    <span class="pay-chip" style="left:688px">Quidlane</span>
  </div>

  <svg class="footer-band" viewBox="0 0 1000 154" aria-hidden="true">
    <path d="M170 154 Q210 30 330 20 L670 20 Q790 30 830 154 Z" fill="var(--band)"/>
    <path d="M170 154 Q210 30 330 20 L670 20 Q790 30 830 154" fill="none" stroke="var(--band-edge)" stroke-width="3" opacity="0.6"/>
  </svg>
  <p class="availability">
    <svg class="smile" viewBox="0 0 20 20" aria-hidden="true"><circle cx="10" cy="10" r="9" fill="#f6c63a"/><circle cx="7" cy="8" r="1.2" fill="#6b4a10"/><circle cx="13" cy="8" r="1.2" fill="#6b4a10"/><path d="M6 12 Q10 15.5 14 12" stroke="#6b4a10" stroke-width="1.3" fill="none"/></svg>Locksmith Available?<span class="availability-yes">YES</span>
  </p>
</main>
</body>
</html>
```